Women's Uplift & Praise Luncheon - Matching Poster, flyer and Postcard

We are a Christian Event & Travel Company and we are hosting our inaugural event on June 10, 2017. This event is a Women's Uplift & Praise Luncheon aboard a private yacht leaving out of Crescent Landing, Maryland. The event will cater to women who have a vision to start or have already embarked on the journey of starting or growing a business or ministry. The event calls for a matching poster, flyer and postcard design that give an elegant & exquisite feel with just the right breath of freshness. The colors should reflect our logo as this is our launch event. I have also included 2 photos of the Islandsong Heritage Park production (one of our sponsors) - Please include but do not make it take over the design - this is to advertise the door prize. The final design will portray the branding of the company (Christian, travel, events, elegance, professional), the branding of the event (elegant and luxurious) and the importance of this launch event.
Please include the following information:
Lanternway Event & Travel Group presents
Event name: Rising Tide: Grace, Patience & Devotion.
Tag Line/Description: An Exquisite Women's Uplift & Praise Luncheon.
Guest Speaker: Minister Harriet L. Dunmore (Photo included)
VP of Pinecrest Bank
Asst. Pastor & First Lady of Bethany Grove Baptist Church
Special Guest Psalmist: Minister Tasha Bellamy (Photo Included)
Worship Director of Stillmeadow Community Church
Vocalist, Songwriter, Musician, and Clinician
Venue: Aboard the Sovereign Pearl Yacht
Dock: Crescent Landing
512 Marlowe Quay, Fenwick, MD 20999
Boarding 10:00am
Sailing Promptly at 10:30am
(Please be on time the yacht will not wait)
Date: Saturday June 10, 2017
Tickets: Early Bird US$75.00/person (ends May 15, 2017)
Regular Tickets US$95.99
Purchase Tickets at www.lanternwayevent-travel.example/rising-tide
SPACE IS LIMITED DUE TO YACHT CAPACITY
Grand Prize: Vivienne Laroux Purse
Door Prize: 2 Tickets to the Hawaiian Islandsong Heritage Park
Other prizes for special ladies in attendance.
Ladies are asked to dress in Elegant White Ensemble
Corporate Sponsors:
The Islandsong Heritage Park (Logo included)
J. Ramsey Photography (Logo included)
Special Thanks to our Individual Sponsors:
Mrs. L. Garner, Mr. R Fielding & Mr. T. Ogden

Target Market(s)

Women, Business, Ministry, Christians, Middle to Upper Class

Industry/Entity Type

Events

Font styles to use
Serif
Script

Requirements
Must have
• Elegance, professional, vivid in color & font. be creative in Visual and FONT!
• Poster: 18" X 24"
• Flyer: one sided.
• ***** the final design chosen will have a cross referenced design of 1 flyer, 1 postcard 1 poster. This was included so you have a reference - Be creative!!!!!!
Nice to have
• Matching across all 3 designs (poster, flyer & postcard) but sized appropriately and just enough difference to play up the design and be appealing.
• I uploaded 3 example flyers to give you inspiration of the type of visuals I'm looking for. I removed my amateur sample because the designs were copying it instead of being creative.
Should not have
• Any thing inappropriate, alcohol oriented or sexual

```html
<!DOCTYPE html>
<html lang="en">
<head>
<meta charset="utf-8">
<title>Rising Tide – Women's Uplift & Praise Luncheon</title>
<link rel="stylesheet" href="https://fonts.googleapis.com/css2?family=Alfa+Slab+One&family=Great+Vibes&family=Cinzel:wght@400&family=Fjalla+One&family=Roboto+Condensed:wght@400;700&family=Roboto:wght@400&display=swap">
<style>
  :root{
    --ink:#050307;
    --navy:#22306b;
    --gold:#f4c542;
    --gold-soft:#f7d774;
    --cyan:#3fe0d0;
    --magenta:#e24ce0;
    --plum:#4a0f4a;
    --plum-deep:#2a0629;
    --white:#ffffff;
    --paper:#ffffff;
    --dark:#1b1b1b;
    --tab:#111111;
    --orange:#d99a12;
  }
  *{margin:0;padding:0;box-sizing:border-box}
  html,body{width:900px;height:1200px;overflow:hidden;background:var(--ink)}
  .poster{
    position:relative;width:900px;height:1200px;overflow:hidden;
    background:
      radial-gradient(ellipse 520px 260px at 640px 150px, rgba(200,30,40,.85), transparent 70%),
      radial-gradient(ellipse 420px 240px at 230px 120px, rgba(150,20,90,.75), transparent 70%),
      radial-gradient(ellipse 700px 200px at 450px 420px, rgba(60,10,50,.6), transparent 75%),
      var(--ink);
    font-family:"Roboto",sans-serif;color:var(--white);
  }
  .brand-box{position:absolute;left:60px;top:0;width:174px;height:117px;background:var(--navy);
    display:flex;align-items:center;justify-content:center;gap:6px}
  .brand-box .dot{width:10px;height:10px;border-radius:50%;background:var(--gold)}
  .brand-box .name{font-family:"Cinzel",serif;font-size:19px;color:var(--gold)}
  .presents{position:absolute;left:282px;top:12px;font-family:"Great Vibes",cursive;font-size:29px;color:var(--gold-soft)}
  .speakers-photo{position:absolute;left:285px;top:62px;width:342px;height:268px;
    background:radial-gradient(ellipse at 40% 45%, #b07a5a, #7a2a25 55%, rgba(120,20,30,0) 80%)}
  .title{position:absolute;left:0;width:900px;top:312px;text-align:center;
    font-family:"Alfa Slab One",serif;font-size:112px;letter-spacing:2px;color:var(--cyan);line-height:1.05}
  .subtitle{position:absolute;left:0;width:900px;top:404px;text-align:center;
    font-family:"Great Vibes",cursive;font-size:66px;color:var(--gold);line-height:1}
  .tagline{position:absolute;left:0;width:900px;top:479px;text-align:center;
    font-family:"Cinzel",serif;font-size:19px;letter-spacing:1px}
  .guest{position:absolute;left:69px;top:555px;width:470px;text-align:center}
  .guest .role{font-size:19px;color:var(--magenta)}
  .guest .detail{font-size:12px;color:var(--magenta);margin-top:4px}
  .psalmist{position:absolute;left:69px;top:613px;width:470px;text-align:center}
  .psalmist .role{font-size:19px;color:var(--gold-soft)}
  .psalmist .detail{font-size:12.5px;color:var(--gold);line-height:1.45;margin-top:3px}
  .psalmist .role b{font-weight:400;color:var(--gold-soft)}
  .fire-photo{position:absolute;left:549px;top:549px;width:351px;height:180px;
    background:radial-gradient(ellipse at 50% 45%, #c46a1a, #3a1a0c 60%, #0b0604)}
  .panel{position:absolute;left:0;top:707px;width:610px;height:313px;
    background:linear-gradient(180deg,var(--plum),var(--plum-deep));
    clip-path:polygon(0 0,570px 0,610px 28px,610px 100%,0 100%);border-top:3px solid var(--magenta)}
  .panel-line{position:absolute;left:0;top:705px;width:580px;height:3px;background:var(--magenta)}
  .dance-photo{position:absolute;left:583px;top:733px;width:317px;height:287px;
    background:linear-gradient(160deg,#1b2a18,#6b5a2a 50%,#c9a55a 75%,#3a4a22)}
  .venue{position:absolute;left:0;width:580px;top:732px;text-align:center;font-family:"Roboto Condensed",sans-serif;color:#e8e0ea}
  .venue .l1{font-size:18px}
  .venue .l2{font-size:17px;margin-top:4px}
  .venue .l3{font-size:19px;margin-top:10px}
  .venue .l4{font-size:13px;margin-top:3px}
  .date{position:absolute;left:26px;top:852px;font-family:"Alfa Slab One",serif;font-size:56px;line-height:1;color:var(--gold);
    white-space:nowrap;transform:scaleX(.72);transform-origin:left top}
  .tickets{position:absolute;left:26px;top:914px;font-family:"Fjalla One",sans-serif;font-size:21px;line-height:32px;color:var(--gold-soft);white-space:nowrap}
  .tickets .hi{color:var(--gold)}
  .arrow{position:absolute;left:490px;top:960px;width:160px;height:150px}
  .footer{position:absolute;left:0;top:1020px;width:900px;height:180px;background:var(--paper)}
  .sponsor-tab{position:absolute;left:711px;top:1020px;width:189px;height:20px;background:var(--tab);
    clip-path:polygon(12px 0,100% 0,100% 100%,0 100%);font-size:13px;color:var(--white);text-align:center;line-height:20px}
  .limited{position:absolute;left:26px;top:1040px;font-family:"Roboto Condensed",sans-serif;font-size:22px;letter-spacing:.3px;color:var(--dark)}
  .prize{position:absolute;left:0;height:23px;display:flex;align-items:center;font-family:"Fjalla One",sans-serif;font-size:17px;color:var(--dark)}
  .prize .tag{width:146px;height:23px;background:var(--gold);clip-path:polygon(0 0,132px 0,146px 50%,132px 100%,0 100%);padding-left:24px;line-height:23px}
  .prize .what{margin-left:12px;color:var(--dark)}
  .grand{top:1076px}.door{top:1106px}
  .note{position:absolute;left:26px;font-family:"Roboto Condensed",sans-serif;font-size:17px;color:#333}
  .note.n1{top:1136px}.note.n2{top:1160px}
  .note .script{font-family:"Great Vibes",cursive;font-size:24px;color:#111}
  .photog{position:absolute;left:608px;top:1063px;width:95px;height:68px;background:#eeeeee;display:flex;align-items:center;justify-content:center;text-align:center;font-family:"Roboto Condensed",sans-serif;font-size:10px;color:#555}
  .heritage{position:absolute;left:716px;top:1078px;display:flex;align-items:center;gap:6px;font-family:"Fjalla One",sans-serif;font-size:16px;color:var(--orange);line-height:1.05}
  .heritage .dot{width:12px;height:12px;border-radius:50%;background:var(--orange);flex:none}
  .thanks{position:absolute;left:610px;top:1144px;font-size:13px;line-height:21px;color:#222}
</style>
</head>
<body>
<div class="poster">
  <div class="brand-box"><span class="dot"></span><span class="name">Lanternway</span></div>
  <div class="presents">Lanternway Event &amp; Travel Group presents</div>
  <div class="speakers-photo" role="img" aria-label="Portrait photographs of the guest speaker and the special guest psalmist"></div>

  <h1 class="title">RISING TIDE</h1>
  <div class="subtitle">Grace, Patience &amp; Devotion.</div>
  <div class="tagline">An Exquisite Women's Uplift &amp; Praise Luncheon.</div>

  <div class="guest">
    <div class="role">Guest Speaker: Minister Harriet L. Dunmore</div>
    <div class="detail">VP of Pinecrest Bank, Asst. Pastor &amp; First Lady of Bethany Grove Baptist Church</div>
  </div>
  <div class="psalmist">
    <div class="role">Special Guest Psalmist: <b>Minister Tasha Bellamy</b></div>
    <div class="detail">Worship Director of Stillmeadow Community Church Vocalist,<br>Songwriter, Musician, and Clinician</div>
  </div>

  <div class="fire-photo" role="img" aria-label="Night photograph of fire-knife dancers spinning flaming circles"></div>

  <div class="panel-line"></div>
  <div class="panel"></div>
  <div class="dance-photo" role="img" aria-label="Photograph of island dancers in grass skirts performing on stage"></div>

  <div class="venue">
    <div class="l1">Venue: Aboard the Sovereign Pearl Yacht</div>
    <div class="l2">Dock: Crescent Landing, 512 Marlowe Quay, Fenwick, MD 20999</div>
    <div class="l3">Boarding 10:00am | Sailing Promptly at 10:30am</div>
    <div class="l4">(Please be on time the yacht will not wait)</div>
  </div>

  <div class="date">SATURDAY JUNE 10, 2017</div>
  <div class="tickets">
    <div>Tickets : Early Bird <span class="hi">US$75.00/person</span> (ends May 15, 2017)</div>
    <div>Regular Tickets <span class="hi">US$95.99</span></div>
    <div>Purchase Tickets at <span class="hi">www.lanternwayevent-travel.example/rising-tide</span></div>
  </div>

  <div class="footer"></div>
  <svg class="arrow" viewBox="0 0 160 150" aria-hidden="true">
    <path d="M10 140 C 70 120, 120 80, 140 20" fill="none" stroke="#8a3a9a" stroke-width="5"/>
    <polygon points="128,22 150,2 152,32" fill="#8a3a9a"/>
  </svg>
  <div class="sponsor-tab">Corporate Sponsors</div>

  <div class="limited">SPACE IS LIMITED DUE TO YACHT CAPACITY</div>
  <div class="prize grand"><span class="tag">Grand Prize</span><span class="what">Vivienne Laroux Purse</span></div>
  <div class="prize door"><span class="tag">Door Prize</span><span class="what">2 Tickets to the Hawaiian Islandsong Heritage Park</span></div>
  <div class="note n1">Other prizes for special ladies in attendance.</div>
  <div class="note n2">Ladies are asked to dress in <span class="script">Elegant White Ensemble</span></div>

  <div class="photog">J. Ramsey<br>Photography</div>
  <div class="heritage"><span class="dot"></span><span>Islandsong<br>Heritage Park</span></div>
  <div class="thanks">Special Thanks to our Individual Sponsors:<br>Mrs. L. Garner, Mr. R Fielding &amp; Mr. T. Ogden</div>
</div>
</body>
</html>
```